Brightmill Data Works

Our company is about IT hardwares and IT solutions. IT hardware such as PC, RAMS, storage and servers. IT solutions such as project management, BA. We are also selling new technology too.

Target Market(s)

Consumer, Small to Medium Business, Corporate

Requirements
Must have
• The business card must have the following:
• Name:
• Title:
• Contact Number:
• Email address:
• Website:
• Color: Must match the logo color upgrade

```html
<!DOCTYPE html>
<html lang="en">
<head>
<meta charset="UTF-8">
<title>Brightmill Data Works – Business Card</title>
<link rel="stylesheet" href="https://fonts.googleapis.com/css2?family=Lato:wght@400;700;900&display=swap">
<style>
  :root {
    --backdrop: #2a2a2a;
    --card: #1b1b1b;
    --card-edge: #232323;
    --amber: #f0a030;
    --amber-deep: #d98a1c;
    --ink-light: #f2f2f2;
    --ink-muted: #5f5f5f;
    --ink-gloss: #0c0c0c;
  }
  * { box-sizing: border-box; margin: 0; padding: 0; }
  html, body {
    width: 1200px; height: 900px; overflow: hidden;
    background: var(--backdrop);
    font-family: "Lato", Arial, sans-serif;
  }
  .stage {
    width: 1200px; height: 900px;
    display: flex; flex-direction: column;
    align-items: center; justify-content: center; gap: 44px;
  }
  .card {
    position: relative;
    width: 640px; height: 366px;
    background: var(--card);
    border-radius: 14px;
    box-shadow: 0 18px 40px rgba(0,0,0,.45);
    overflow: hidden;
  }
  /* Front */
  .card-front {
    display: flex; align-items: center; justify-content: center;
  }
  .wordmark {
    display: flex; align-items: center; gap: 14px;
  }
  .wordmark-dot {
    width: 22px; height: 22px; border-radius: 50%;
  }
  .wordmark-name {
    font-weight: 900; font-size: 38px; letter-spacing: 1px;
    text-transform: uppercase;
  }
  .card-front .wordmark-dot { background: var(--ink-gloss); }
  .card-front .wordmark-name { color: var(--ink-gloss); }

  /* Back */
  .card-back .brand {
    position: absolute; left: 0; top: 0;
    width: 330px; height: 100%;
    display: flex; align-items: center; justify-content: center;
  }
  .card-back .wordmark-dot { width: 16px; height: 16px; background: var(--amber); }
  .card-back .wordmark-name { font-size: 24px; color: var(--ink-muted); }
  .divider {
    position: absolute; left: 340px; top: 92px;
    width: 2px; height: 150px; background: var(--amber);
  }
  .contact {
    position: absolute; left: 372px; top: 86px;
  }
  .contact-name {
    color: var(--amber); font-size: 19px; font-weight: 400;
    text-transform: uppercase; letter-spacing: .3px;
  }
  .contact-name strong { font-weight: 700; }
  .contact-title {
    color: var(--ink-light); font-size: 12.5px; margin-top: 3px;
  }
  .contact-list { list-style: none; margin-top: 22px; }
  .contact-list li {
    display: flex; align-items: center; gap: 10px;
    color: var(--ink-light); font-size: 13.5px; margin-bottom: 9px;
  }
  .contact-list svg { width: 15px; height: 13px; flex: none; }
  .contact-web {
    color: var(--amber); font-weight: 700; font-size: 15px; margin-top: 8px;
  }
  .edge-band {
    position: absolute; left: 0; bottom: 0; width: 100%; height: 8px;
    background: linear-gradient(90deg, var(--amber-deep), var(--amber));
  }
</style>
</head>
<body>
<main class="stage">
  <section class="card card-front" aria-label="Card front">
    <div class="wordmark">
      <span class="wordmark-dot"></span>
      <span class="wordmark-name">Brightmill Data Works</span>
    </div>
  </section>

  <section class="card card-back" aria-label="Card back">
    <div class="brand">
      <div class="wordmark">
        <span class="wordmark-dot"></span>
        <span class="wordmark-name">Brightmill Data Works</span>
      </div>
    </div>
    <div class="divider"></div>
    <div class="contact">
      <p class="contact-name">Daniel <strong>Harrow</strong></p>
      <p class="contact-title">Managing Director</p>
      <ul class="contact-list">
        <li>
          <svg viewBox="0 0 16 14" aria-hidden="true"><path fill="#f0a030" d="M1 4c0-2 2-3 7-3s7 1 7 3v1h-4V3.5H5V5H1zM3 6h10l1.5 7h-13z"/><circle cx="8" cy="9.5" r="2" fill="#1b1b1b"/></svg>
          01632 960482
        </li>
        <li>
          <svg viewBox="0 0 16 12" aria-hidden="true"><rect x=".5" y=".5" width="15" height="11" fill="#f0a030"/><path d="M1 1l7 6 7-6" fill="none" stroke="#1b1b1b" stroke-width="1.4"/></svg>
          hello@brightmilldata.co.uk
        </li>
      </ul>
      <p class="contact-web">www.brightmilldata.co.uk</p>
    </div>
    <div class="edge-band"></div>
  </section>
</main>
</body>
</html>
```